Business Card Design - Amberfield Court

We are looking at a new design for our business cards that has a modern and professional look. We run a residential aged care facility focussing on the care of residents. The cards will be used for potential clients, consultants and business opportunities in this sector. Blue and white is our main colours and would to see these colours incorporated in the design.
Industry/Entity Type
Business
Contact Information for Business Card
Amberfield Court, Darren Walsh, dwalsh@amberfieldcourt.com.au, Finance Manager, 0472 639 208, BCom, 37 Marrabel Crescent, Brindle Vale, Qld 4093.
Look and feel
Each slider illustrates characteristics of the customer's brand and the style your logo design should communicate.

```html
<!DOCTYPE html>
<html lang="en">
<head>
<meta charset="utf-8">
<title>Amberfield Court – Business Card</title>
<link rel="stylesheet" href="https://fonts.googleapis.com/css2?family=Arimo:ital,wght@0,400;0,700;1,400&family=Oswald:wght@300;400&display=swap">
<style>
  :root {
    --page-bg: #e9e7e3;
    --card-blue-dark: #3f7089;
    --card-blue: #4f8099;
    --card-blue-light: #7fa7bb;
    --card-white: #ffffff;
    --card-grey: #d9d9d9;
    --logo-blue: #46758d;
    --figure-tone: #cfdde5;
    --figure-tone-soft: #e9f0f4;
    --text-white: #ffffff;
  }
  * { box-sizing: border-box; margin: 0; padding: 0; }
  html, body {
    width: 1200px;
    height: 950px;
    overflow: hidden;
    background: var(--page-bg);
  }
  .canvas {
    width: 1200px;
    height: 950px;
    display: flex;
    flex-direction: column;
    align-items: center;
    justify-content: center;
    gap: 50px;
  }
  .card {
    width: 720px;
    height: 410px;
    position: relative;
    overflow: hidden;
    box-shadow: 0 10px 28px rgba(0,0,0,0.18);
  }

  /* Front side */
  .card-front {
    background: linear-gradient(100deg, var(--card-blue-dark) 0%, var(--card-blue) 50%, var(--card-blue-light) 100%);
    color: var(--text-white);
    font-family: "Arimo", Arial, sans-serif;
  }
  .brand-block {
    position: absolute;
    left: 44px;
    top: 40px;
  }
  .brand-name {
    font-family: "Oswald", "Arial Narrow", sans-serif;
    font-weight: 300;
    font-size: 34px;
    letter-spacing: 4px;
    text-transform: uppercase;
    line-height: 1;
  }
  .tagline {
    font-style: italic;
    font-size: 19px;
    margin-top: 6px;
    letter-spacing: 0.3px;
  }
  .contact-block {
    position: absolute;
    left: 44px;
    top: 148px;
    font-size: 17px;
    line-height: 1.32;
  }
  .person-name {
    font-weight: 700;
    font-size: 20px;
    text-transform: uppercase;
  }
  .person-name .credential { font-size: 16px; }
  .person-role {
    text-transform: uppercase;
    margin-bottom: 12px;
  }
  .address { margin-bottom: 12px; }
  .figure-area {
    position: absolute;
    right: 30px;
    bottom: 0;
    width: 330px;
    height: 210px;
  }

  /* Back side */
  .card-back {
    background: linear-gradient(115deg, var(--card-white) 0%, var(--card-white) 45%, var(--card-grey) 100%);
    display: flex;
    align-items: center;
    justify-content: center;
  }
  .back-mark {
    display: flex;
    align-items: center;
    gap: 18px;
  }
  .back-dot {
    width: 44px;
    height: 44px;
    border-radius: 50%;
    background: var(--logo-blue);
  }
  .back-name {
    font-family: "Oswald", "Arial Narrow", sans-serif;
    font-weight: 400;
    font-size: 40px;
    letter-spacing: 4px;
    text-transform: uppercase;
    color: var(--logo-blue);
  }
</style>
</head>
<body>
<main class="canvas">
  <section class="card card-front" aria-label="Business card front">
    <header class="brand-block">
      <h1 class="brand-name">Amberfield Court</h1>
      <p class="tagline">Comfort, Respect, Belonging</p>
    </header>
    <div class="contact-block">
      <p class="person-name">Darren Walsh <span class="credential">BCom</span></p>
      <p class="person-role">Finance Manager</p>
      <p class="address">37 Marrabel Crescent<br>Brindle Vale, Qld 4093.</p>
      <p class="phone">0472 639 208</p>
      <p class="email">dwalsh@amberfieldcourt.com.au</p>
      <p class="web">www.amberfieldcourt.com.au</p>
    </div>
    <svg class="figure-area" viewBox="0 0 330 210" role="img" aria-label="Soft silhouette illustration of a carer sitting beside a resident">
      <defs>
        <linearGradient id="figureFill" x1="0" y1="0" x2="0" y2="1">
          <stop offset="0" stop-color="var(--figure-tone-soft)" stop-opacity="0.55"/>
          <stop offset="1" stop-color="var(--figure-tone)" stop-opacity="0.95"/>
        </linearGradient>
      </defs>
      <path d="M0 210 L0 110 Q0 20 90 20 L240 20 Q330 20 330 110 L330 210 Z" fill="url(#figureFill)"/>
    </svg>
  </section>

  <section class="card card-back" aria-label="Business card back">
    <div class="back-mark">
      <span class="back-dot" aria-hidden="true"></span>
      <span class="back-name">Amberfield Court</span>
    </div>
  </section>
</main>
</body>
</html>
```